Dwelvano - "Where Pest Control is Free for Life..." Please see pitch deck...

Project goal, that this is a reusable template, not a one-off card
Brand and design direction, follow the logo, use the brand palette (with a color swatch table), typography and layout guidance
The John Doe placeholder content as a clean field-by-field table (name, title, company, address, office, cell, fax, email, dwelvano.com)
Print specs, 3.5 × 2 in trim, 0.125 in bleed, 300 DPI, CMYK, crop marks
Deliverables, layered editable PSD (your primary ask) plus vector .AI/.EPS and a press-ready PDF/X-1a, with fonts packaged
What you'll provide (logo, colors, fonts)
Process and sign-off, concept first, then full file package on approval.
Populate every field with this John Doe placeholder data so we can see the layout fully built out. We will replace it per person.
Name John Doe
Title Title / Position
Company Dwelvano
Address 48 Harbor Lane, Suite 210, Pensacola, FL 32502
Office (555) 014-2200
Cell (555) 014-2231
Fax (555) 014-2290
Email johndoe@dwelvano.com
Website dwelvano.com

We need the working, editable source files so we can update them ourselves, plus a ready-to-print export:
1. Photoshop (.PSD) — fully layered and editable, with each contact field on its own labeled text layer. This is the primary requested format.
2. Vector source — the press-standard editable format, Adobe Illustrator (.AI) and/or .EPS, since vector is preferred for crisp text and logos at print.
3. Print-ready PDF — press-quality (PDF/X-1a), CMYK, with bleed and crop marks, both sides.
4. Packaged fonts and links — include or list all fonts used, and package any linked assets so the files open correctly on our end.

Why both PSD and vector
The PSD covers our request directly and is easy for us to edit. Vector (.AI/.EPS) is what most commercial printers actually prefer for type and logos because it stays razor-sharp at any size. Providing both keeps us flexible no matter which printer we use. Have fun and keep it modern and cool the designer of the logo did a great job, see what you can do.

```html
<!DOCTYPE html>
<html lang="en">
<head>
<meta charset="utf-8">
<title>Dwelvano Business Card</title>
<link rel="stylesheet" href="https://fonts.googleapis.com/css2?family=Montserrat:wght@400;500;600;700;800&display=swap">
<style>
  :root{
    --stage:#3b3b3d;
    --navy:#0b1228;
    --cyan:#12b2c4;
    --cyan-soft:#cdeef1;
    --white:#ffffff;
    --ink:#1b2236;
    --text-grey:#4a4f5c;
  }
  *{box-sizing:border-box;margin:0;padding:0}
  html,body{width:1200px;height:875px;overflow:hidden}
  body{
    background:var(--stage);
    font-family:"Montserrat",sans-serif;
    position:relative;
  }
  .card{
    position:absolute;
    top:283px;
    width:540px;
    height:309px;
    border-radius:18px;
    overflow:hidden;
    box-shadow:0 14px 30px rgba(0,0,0,.35);
  }
  /* Front */
  .card--front{left:40px;background:var(--navy)}
  .brand{
    position:absolute;left:0;right:0;top:92px;
    text-align:center;
    color:var(--white);
  }
  .brand__name{
    font-weight:800;
    font-size:78px;
    letter-spacing:-1px;
    line-height:1;
  }
  .brand__tagline{
    margin-top:10px;
    font-weight:700;
    font-size:15px;
    letter-spacing:2.4px;
  }
  .brand__sub{
    margin-top:4px;
    font-weight:500;
    font-size:13px;
    letter-spacing:.8px;
    color:var(--cyan);
  }
  /* Back */
  .card--back{left:620px;background:var(--white)}
  .back__panel{
    position:absolute;
    right:-20px;top:-20px;
    width:220px;height:349px;
    background:var(--cyan-soft);
    border-radius:40px;
  }
  .back__tab{
    position:absolute;left:0;top:80px;
    width:14px;height:34px;
    background:var(--cyan);
    border-radius:0 6px 6px 0;
  }
  .identity{position:absolute;left:34px;top:70px}
  .identity__name{
    font-weight:700;
    font-size:27px;
    letter-spacing:.5px;
    color:var(--ink);
    line-height:1.05;
  }
  .identity__surname{color:var(--cyan)}
  .identity__company{
    font-size:14px;
    font-weight:500;
    color:var(--text-grey);
    margin-top:2px;
  }
  .address{
    position:absolute;left:64px;top:145px;
    font-style:normal;
    font-size:11.5px;
    line-height:1.4;
    color:var(--text-grey);
  }
  .contacts{
    position:absolute;left:64px;top:190px;
    list-style:none;
    font-size:11.5px;
    color:var(--text-grey);
  }
  .contacts__item{
    display:flex;align-items:center;gap:7px;
    line-height:18px;
  }
  .contacts__icon{width:10px;height:10px;fill:var(--cyan);flex:none}
</style>
</head>
<body>

<section class="card card--front" aria-label="Card front">
  <div class="brand">
    <div class="brand__name">Dwelvano</div>
    <div class="brand__tagline">WE SERVE WHERE YOU SETTLE</div>
    <div class="brand__sub">A friendlier local service</div>
  </div>
</section>

<section class="card card--back" aria-label="Card back">
  <div class="back__panel"></div>
  <div class="back__tab"></div>

  <div class="identity">
    <div class="identity__name">JOHN <span class="identity__surname">DOE</span></div>
    <div class="identity__company">Company Dwelvano</div>
  </div>

  <address class="address">
    48 Harbor Lane, Suite 210<br>
    Pensacola, FL 32502
  </address>

  <ul class="contacts">
    <li class="contacts__item">
      <svg class="contacts__icon" viewBox="0 0 10 10"><path d="M2 0.5l2 2-1 1.2c.6 1.3 1.6 2.3 2.9 2.9L7 5.6l2 2-1.2 1.6C4.5 9 1 5.5 .8 1.8z"/></svg>
      (555) 014-2200
    </li>
    <li class="contacts__item">
      <svg class="contacts__icon" viewBox="0 0 10 10"><path d="M2.8 0h4.4c.4 0 .8.4.8.8v8.4c0 .4-.4.8-.8.8H2.8c-.4 0-.8-.4-.8-.8V.8c0-.4.4-.8.8-.8zM3 1.2v6.6h4V1.2z"/></svg>
      (555) 014-2231
    </li>
    <li class="contacts__item">
      <svg class="contacts__icon" viewBox="0 0 10 10"><path d="M2.5 0h5v3h-5zM1 3.5h8c.5 0 1 .5 1 1V8H8v2H2V8H0V4.5c0-.5.5-1 1-1zM3 6.5v2.5h4V6.5z"/></svg>
      (555) 014-2290
    </li>
    <li class="contacts__item">
      <svg class="contacts__icon" viewBox="0 0 10 10"><path d="M0 2h10v6H0zM1 3v.3l4 2.6 4-2.6V3L5 5.5z"/></svg>
      johndoe@dwelvano.com
    </li>
    <li class="contacts__item">
      <svg class="contacts__icon" viewBox="0 0 10 10"><circle cx="5" cy="5" r="5"/></svg>
      dwelvano.com
    </li>
  </ul>
</section>

</body>
</html>
```